Business Card Design For Marketing Agnecy LVP

Need business card design for marketing agency.

Doug Fenwick
President, CEO
1-555-302-4196
doug@boldpromoperksgroup.example
www.BoldPromoPerksGroup.example

Back Side:
Boost Sales Using Rewards, Incentives & Giveaways
Get A Free Sample Package

Target Market(s)

B2B

Industry/Entity Type

Marketing

Contact Information for Business Card

Doug Fenwick
President, CEO
1-555-302-4196

Back Side:
Get A Free Sample Package

Please note that my current url is OLD DESIGN. I am working on new design and want the business card to match color themes at least on new site. Here is the demo link for new site so you can see the colors I use, etc.

http://layoutcratehub.example/kq/doug/lvp_final/index.html

Requirements
Must have
• Please note that my current url is OLD DESIGN. I am working on new design and want the business card to match color themes at least on new site. Here is the demo link for new site so you can see the colors I use, etc.

Nice to have

Should not have

```html
<!DOCTYPE html>
<html lang="en">
<head>
<meta charset="utf-8">
<title>LVP Business Card</title>
<link rel="stylesheet" href="https://fonts.googleapis.com/css2?family=Montserrat:wght@500;700;800&family=Arimo:wght@400;700&display=swap">
<style>
  :root {
    --brand-blue: #1077c0;
    --ink-grey: #58585a;
    --paper: #ffffff;
    --backdrop: #2c3036;
  }
  * { box-sizing: border-box; margin: 0; padding: 0; }
  html, body { width: 1200px; height: 1000px; overflow: hidden; }
  body {
    background: var(--backdrop);
    position: relative;
    font-family: "Arimo", Arial, sans-serif;
  }
  .card {
    position: absolute;
    left: 220px;
    width: 760px;
    height: 434px;
    border-radius: 22px;
    overflow: hidden;
    background: var(--brand-blue);
  }
  .card--brand { top: 48px; }
  .card--contact { top: 518px; }

  /* Brand side */
  .brand-mark {
    position: absolute;
    left: 0; right: 0; top: 80px;
    text-align: center;
    font-family: "Montserrat", Arial, sans-serif;
    font-weight: 800;
    font-size: 150px;
    letter-spacing: 4px;
    color: var(--paper);
    line-height: 1;
  }
  .brand-url {
    position: absolute;
    left: 0; right: 0; top: 318px;
    text-align: center;
    font-family: "Montserrat", Arial, sans-serif;
    font-weight: 500;
    font-size: 17px;
    color: var(--paper);
  }
  .tagline-band {
    position: absolute;
    left: 0; right: 0; top: 352px;
    height: 40px;
    background: var(--paper);
    display: flex; align-items: center; justify-content: center;
    font-family: "Montserrat", Arial, sans-serif;
    font-weight: 500;
    font-size: 17px;
    color: var(--ink-grey);
    letter-spacing: 0.4px;
  }
  .tagline-band .sep { margin: 0 6px; }

  /* Contact side */
  .contact-shape { position: absolute; inset: 0; }
  .holder {
    position: absolute; left: 52px; top: 56px;
    color: var(--paper);
  }
  .holder-name {
    font-family: "Montserrat", Arial, sans-serif;
    font-weight: 800;
    font-size: 28px;
    letter-spacing: 0.5px;
  }
  .holder-title { font-size: 21px; margin-top: 4px; }
  .contact-list {
    position: absolute; left: 40px; bottom: 48px;
    list-style: none;
    color: var(--paper);
    font-size: 17px;
  }
  .contact-list li { display: flex; align-items: center; gap: 12px; height: 32px; white-space: nowrap; }
  .contact-list svg { width: 20px; height: 20px; flex: none; }
  .contact-logo {
    position: absolute; left: 480px; top: 160px; width: 260px;
    text-align: center;
  }
  .contact-logo .wordmark {
    font-family: "Montserrat", Arial, sans-serif;
    font-weight: 800;
    font-size: 96px;
    line-height: 1;
    color: var(--brand-blue);
    letter-spacing: 2px;
  }
</style>
</head>
<body>
  <section class="card card--brand" aria-label="Card back">
    <div class="brand-mark">LVP</div>
    <div class="brand-url">www.BoldPromoPerksGroup.example</div>
    <div class="tagline-band">
      Boost Sales Using Rewards<span class="sep">|</span>Incentives &amp; Giveaways<span class="sep">|</span>Get A Free Sample Package
    </div>
  </section>

  <section class="card card--contact" aria-label="Card front">
    <svg class="contact-shape" viewBox="0 0 760 434" preserveAspectRatio="none" aria-hidden="true">
      <path d="M560 0 C 465 60, 415 170, 425 280 C 430 350, 450 400, 475 434 L 760 434 L 760 0 Z" fill="var(--ink-grey)"/>
      <path d="M585 0 C 490 60, 440 170, 450 280 C 455 350, 475 400, 502 434 L 760 434 L 760 0 Z" fill="var(--paper)"/>
    </svg>
    <div class="holder">
      <div class="holder-name">DOUG FENWICK</div>
      <div class="holder-title">President, CEO</div>
    </div>
    <div class="contact-logo">
      <span class="wordmark">LVP</span>
    </div>
    <ul class="contact-list">
      <li>
        <svg viewBox="0 0 22 22"><rect width="22" height="22" rx="3" fill="#fff"/><path d="M7 5l2.5 0 1 3-1.5 1.2a8 8 0 0 0 3.8 3.8L14 11.5l3 1V15a1.5 1.5 0 0 1-1.5 1.5A10 10 0 0 1 5.5 6.5 1.5 1.5 0 0 1 7 5z" fill="var(--brand-blue)"/></svg>
        1-555-302-4196
      </li>
      <li>
        <svg viewBox="0 0 22 22"><rect width="22" height="22" rx="3" fill="#fff"/><rect x="4" y="6.5" width="14" height="9" fill="none" stroke="var(--brand-blue)" stroke-width="1.6"/><path d="M4 6.5l7 5.5 7-5.5" fill="none" stroke="var(--brand-blue)" stroke-width="1.6"/></svg>
        doug@boldpromoperksgroup.example
      </li>
      <li>
        <svg viewBox="0 0 22 22"><rect width="22" height="22" rx="3" fill="#fff"/><circle cx="11" cy="11" r="6" fill="none" stroke="var(--brand-blue)" stroke-width="1.6"/><path d="M5 11h12M11 5c-3 3-3 9 0 12M11 5c3 3 3 9 0 12" fill="none" stroke="var(--brand-blue)" stroke-width="1.2"/></svg>
        www.BoldPromoPerksGroup.example
      </li>
    </ul>
  </section>
</body>
</html>
```